Wandering Rooms Stationary Set

Wandering Rooms is a bespoke interior design firm set to provide services to VIP clients with elegance and minimalism is the main theme for our stationary set. We require a full stationary set covering A4 letterhead, A4 & A3 envelopes, business cards, USB's, CDs, email signature and any other item the designer sees fit. logo is already designed and finalized, and we require the designer to use it as is without modifying the logo.

Address to be used on letterhead / business cards ...etc shall be as follows:

Phone : +971 2 518 2047
P.O. Box : 309186
Address: Block C&D, Bldg. 47, Court 12, Abu Dhabi, United Arab Emirates
Website: www.wanderingrooms-example.com

Target Market(s)

VIP Clients

Industry/Entity Type

Interior Design

Font styles to use
Other font styles liked:
• something to be unique

Colors

Designer to choose colors to be used in the design.

Requirements
Must have
• Elegant, minimalistic
Nice to have
• Simple yet elegant design having a sharp yet clean cut format
Should not have
• No additional colours, just colours that are used in the logo (silver, black or gold)

```html
<!DOCTYPE html>
<html lang="en">
<head>
<meta charset="utf-8">
<title>Wandering Rooms Stationery Set</title>
<link href="https://fonts.googleapis.com/css2?family=Cormorant+Garamond:wght@400;500&family=Jost:wght@400&display=swap" rel="stylesheet">
<style>
  :root {
    --bg-top: #8b8781;
    --bg-bottom: #4e4a45;
    --gold: #b5955a;
    --ink: #555049;
    --paper-light: #ffffff;
    --paper-dark: #c6c6c6;
    --label: #f4f2ee;
  }
  * { margin: 0; padding: 0; box-sizing: border-box; }
  html, body { width: 1200px; height: 919px; overflow: hidden; }
  body {
    position: relative;
    background: linear-gradient(180deg, var(--bg-top) 0%, var(--bg-bottom) 100%);
    font-family: "Cormorant Garamond", Georgia, serif;
    color: var(--ink);
  }
  .piece {
    position: absolute;
    background: linear-gradient(150deg, var(--paper-light) 15%, var(--paper-dark) 100%);
    box-shadow: 0 2px 5px rgba(0,0,0,0.25);
  }
  .card { border-radius: 6px; width: 206px; height: 118px; top: 74px; }
  .card-front { left: 81px; background: linear-gradient(160deg, #f6f6f6 20%, #c9c9c9 100%); }
  .card-back { left: 308px; background: var(--gold); display: flex; align-items: center; justify-content: center; }
  .label {
    position: absolute;
    font-family: "Jost", Arial, sans-serif;
    font-size: 10px;
    letter-spacing: 0.3px;
    color: var(--label);
    transform: translateX(-50%);
    white-space: nowrap;
  }
  .wordmark {
    font-family: "Cormorant Garamond", Georgia, serif;
    font-weight: 400;
    color: var(--gold);
    white-space: nowrap;
    line-height: 1;
  }
  .card-back .wordmark { color: #ffffff; font-size: 17px; }
  .abs { position: absolute; }
  .divider { position: absolute; width: 0.6px; background: #8a8580; }
  .contact { position: absolute; font-size: 4.4px; line-height: 1.5; color: var(--ink); white-space: nowrap; }
  .contact .row { display: flex; align-items: center; gap: 2.5px; }
  .contact svg { width: 4px; height: 4px; fill: var(--gold); flex: none; }
  .holder-name { font-size: 8px; color: var(--gold); line-height: 1.2; }
  .holder-role { font-size: 4.8px; margin-bottom: 3px; }
  .letter { left: 84px; top: 226px; width: 430px; height: 610px; }
  .letter .contact { font-size: 5px; }
  .env-a4-front { left: 559px; top: 78px; width: 254px; height: 360px; }
  .env-a4-back { left: 847px; top: 78px; width: 255px; height: 360px; }
  .env-a3-front { left: 558px; top: 470px; width: 260px; height: 367px; }
  .env-a3-back { left: 845px; top: 470px; width: 260px; height: 367px; }
  .flap { position: absolute; left: 0; top: 0; width: 100%; height: 35px; }
  .flap-mark { position: absolute; left: 0; right: 0; top: 15px; text-align: center; font-size: 6px; color: #ffffff; }
  .env-address { position: absolute; font-size: 3.6px; line-height: 1.5; white-space: nowrap; }
</style>
</head>
<body>

  <!-- Business card front -->
  <section class="piece card card-front">
    <div class="wordmark abs" style="left:20px; top:54px; font-size:11px;">Wandering Rooms</div>
    <div class="divider" style="left:110px; top:30px; height:58px;"></div>
    <div class="contact" style="left:117px; top:31px;">
      <div class="holder-name">Daniel Hart</div>
      <div class="holder-role">President</div>
      <div>P.O. Box : 309186,</div>
      <div>Block C&amp;D, Bldg. 47, Court 12</div>
      <div style="margin-bottom:3px;">Abu Dhabi, United Arab Emirates</div>
      <div class="row"><svg viewBox="0 0 10 10"><path d="M2 0.5l2 2-1 1.3c.6 1.4 1.7 2.5 3.2 3.2L7.5 6l2 2-1.3 1.5C4.5 9.5.5 5.5.5 1.8z"/></svg>+971 2 518 2047</div>
      <div class="row"><svg viewBox="0 0 10 10"><rect x="0.5" y="2" width="9" height="6"/></svg>info@wanderingrooms-example.com</div>
      <div class="row"><svg viewBox="0 0 10 10"><circle cx="5" cy="5" r="4.5"/></svg>www.wanderingrooms-example.com</div>
    </div>
  </section>
  <div class="label" style="left:193px; top:200px;">CARD FRONT</div>

  <!-- Business card back -->
  <section class="piece card card-back">
    <div class="wordmark">Wandering Rooms</div>
  </section>
  <div class="label" style="left:397px; top:200px;">CARD BACK</div>

  <!-- A4 letterhead -->
  <section class="piece letter">
    <div class="wordmark abs" style="left:32px; top:51px; font-size:14px;">Wandering Rooms</div>
    <div class="divider" style="left:315px; top:33px; height:62px;"></div>
    <div class="contact" style="left:326px; top:35px;">
      <div>P.O. Box : 309186,</div>
      <div>Block C&amp;D, Bldg. 47, Court 12</div>
      <div style="margin-bottom:3px;">Abu Dhabi, United Arab Emirates</div>
      <div class="row"><svg viewBox="0 0 10 10"><path d="M2 0.5l2 2-1 1.3c.6 1.4 1.7 2.5 3.2 3.2L7.5 6l2 2-1.3 1.5C4.5 9.5.5 5.5.5 1.8z"/></svg>+971 2 518 2047</div>
      <div class="row"><svg viewBox="0 0 10 10"><rect x="0.5" y="2" width="9" height="6"/></svg>info@wanderingrooms-example.com</div>
      <div class="row"><svg viewBox="0 0 10 10"><circle cx="5" cy="5" r="4.5"/></svg>www.wanderingrooms-example.com</div>
    </div>
  </section>
  <div class="label" style="left:299px; top:853px;">A4 LETTER</div>

  <!-- A4 envelope front -->
  <section class="piece env-a4-front">
    <div class="wordmark abs" style="left:25px; top:48px; font-size:8px;">Wandering Rooms</div>
    <div class="env-address" style="left:25px; top:67px;">
      <div>P.O. Box : 309186,</div>
      <div>Block C&amp;D, Bldg. 47, Court 12</div>
      <div>Abu Dhabi, United Arab Emirates</div>
    </div>
  </section>
  <div class="label" style="left:696px; top:447px;">A4 ENVELOPE FRONT</div>

  <!-- A4 envelope back -->
  <section class="piece env-a4-back">
    <svg class="flap" viewBox="0 0 255 35" preserveAspectRatio="none" aria-hidden="true">
      <path d="M0 0H255L247 22Q243 35 228 35H27Q12 35 8 22Z" fill="var(--gold)"/>
    </svg>
    <div class="wordmark flap-mark">Wandering Rooms</div>
  </section>
  <div class="label" style="left:977px; top:447px;">A4 ENVELOPE BACK</div>

  <!-- A3 envelope front -->
  <section class="piece env-a3-front">
    <div class="wordmark abs" style="left:28px; top:38px; font-size:8px;">Wandering Rooms</div>
    <div class="env-address" style="left:28px; top:58px;">
      <div>P.O. Box : 309186,</div>
      <div>Block C&amp;D, Bldg. 47, Court 12</div>
      <div>Abu Dhabi, United Arab Emirates</div>
    </div>
  </section>
  <div class="label" style="left:696px; top:853px;">A3 ENVELOPE FRONT</div>

  <!-- A3 envelope back -->
  <section class="piece env-a3-back">
    <svg class="flap" viewBox="0 0 260 35" preserveAspectRatio="none" aria-hidden="true">
      <path d="M0 0H260L252 22Q248 35 233 35H27Q12 35 8 22Z" fill="var(--gold)"/>
    </svg>
    <div class="wordmark flap-mark">Wandering Rooms</div>
  </section>
  <div class="label" style="left:977px; top:853px;">A3 ENVELOPE BACK</div>

</body>
</html>
```